Business Card Design Project

I need a business card designed from scratch. I have an existing logo that I can upload in Illustrator for modification or redesign.

The Company is called Query Lanterns http://querylanterns.com.au and we provide Search Engine Optimization services to Australian businesses. The current logo signifies an increase in visitors, profits etc...

There are no restrictions as to the redesign - colours, style etc are all open to change.

Cards will be full colour and one sided printed at http://www.cardmoxel.com.au so check their requirements for file format and sizes etc.

I will expect all original files upon completion of project.

Target Market(s)

Any business with a web site looking to improve their search engine rankings

Industry/Entity Type

Business

Requirements
Must have
• I like modern, sleek designs. Clean, not fussy, uncluttered.

```html
<!DOCTYPE html>
<html lang="en">
<head>
<meta charset="utf-8">
<title>Query Lanterns – Business Card</title>
<link href="https://fonts.googleapis.com/css2?family=Source+Sans+3:wght@400;600;700;800&display=swap" rel="stylesheet">
<style>
  :root {
    --brand-blue: #1a6db5;
    --brand-blue-dark: #1560a4;
    --band-top: #3b8fd3;
    --band-bottom: #1463ac;
    --accent-yellow: #f6c312;
    --card-white: #ffffff;
    --ink-grey: #444a52;
    --stage: #ececec;
  }
  * { box-sizing: border-box; margin: 0; padding: 0; }
  html, body {
    width: 1200px; height: 460px; overflow: hidden;
    background: var(--stage);
    font-family: "Source Sans 3", "Myriad Pro", Arial, sans-serif;
  }
  .canvas { position: relative; width: 1200px; height: 460px; }

  .card {
    position: absolute; top: 75px; width: 542px; height: 310px;
    background: var(--card-white); border-radius: 14px; overflow: hidden;
    box-shadow: 0 2px 6px rgba(0,0,0,0.18);
  }
  .card--front { left: 44px; }
  .card--back { left: 613px; }

  .wordmark {
    position: absolute; left: 0; right: 0;
    display: flex; align-items: center; justify-content: center; gap: 12px;
  }
  .wordmark__dot {
    width: 16px; height: 16px; border-radius: 50%;
    background: var(--accent-yellow);
  }
  .wordmark__name {
    font-weight: 800; font-size: 40px; color: var(--brand-blue);
    letter-spacing: -0.5px; line-height: 1;
  }
  .card--front .wordmark { top: 80px; }
  .card--back .wordmark { top: 115px; }

  .holder {
    position: absolute; top: 182px; left: 0; right: 0; text-align: center;
    color: var(--brand-blue); font-size: 18px; font-weight: 700;
  }
  .holder__title { color: var(--ink-grey); font-weight: 400; font-size: 14px; }

  .accent-rule {
    position: absolute; top: 228px; left: 0; right: 0; height: 3px;
    background: var(--accent-yellow);
  }
  .contact-band {
    position: absolute; top: 233px; left: 0; right: 0; bottom: 0;
    background: linear-gradient(180deg, var(--band-top), var(--band-bottom));
    display: flex; gap: 12px; padding: 19px 0 0 21px;
    color: #fff; font-size: 13.5px; line-height: 20px;
  }
  .contact-band__col { white-space: nowrap; }
  .contact-band__item { display: flex; align-items: center; gap: 5px; }
  .contact-band__item svg { width: 10px; height: 10px; flex: none; }

  .web-address {
    position: absolute; top: 201px; left: 0; right: 0; text-align: center;
    font-size: 13.5px; letter-spacing: 2px; color: var(--ink-grey);
  }
  .web-address span { color: var(--brand-blue); }
</style>
</head>
<body>
<main class="canvas">

  <section class="card card--front" aria-label="Card front">
    <div class="wordmark">
      <span class="wordmark__dot"></span>
      <span class="wordmark__name">Query Lanterns</span>
    </div>

    <p class="holder">Your Name / <span class="holder__title">Title</span></p>

    <div class="accent-rule"></div>

    <div class="contact-band">
      <div class="contact-band__col">
        <p>00Floor Street, City Name</p>
        <p>State Name, Contry Name</p>
      </div>
      <div class="contact-band__col">
        <p class="contact-band__item">
          <svg viewBox="0 0 10 10"><path d="M2 1 L4 1 L4.6 3 L3.4 3.8 Q4.4 5.8 6.2 6.6 L7 5.4 L9 6 L9 8 Q8.5 9 7.5 9 Q1 8.2 1 2.5 Q1 1.5 2 1Z" fill="#fff"/></svg>
          012 345 6789</p>
        <p class="contact-band__item">
          <svg viewBox="0 0 10 10"><rect x="2.5" y="0.5" width="5" height="9" rx="1" fill="#fff"/><rect x="3.4" y="1.6" width="3.2" height="5.4" fill="#2a7cc4"/></svg>
          012 345 6789</p>
      </div>
      <div class="contact-band__col">
        <p class="contact-band__item">
          <svg viewBox="0 0 10 10"><rect x="0.5" y="2" width="9" height="6" rx="0.8" fill="#fff"/><path d="M0.8 2.4 L5 5.4 L9.2 2.4" stroke="#2a7cc4" stroke-width="0.8" fill="none"/></svg>
          enquiry@querylanterns.com.au</p>
        <p class="contact-band__item">
          <svg viewBox="0 0 10 10"><circle cx="5" cy="5" r="4.2" fill="#fff"/></svg>
          www.querylanterns.com.au</p>
      </div>
    </div>
  </section>

  <section class="card card--back" aria-label="Card back">
    <div class="wordmark">
      <span class="wordmark__dot"></span>
      <span class="wordmark__name">Query Lanterns</span>
    </div>
    <p class="web-address">www.<span>querylanterns</span>.com.au</p>
  </section>

</main>
</body>
</html>
```